Founder / concept developer needs business card // Consultant needs VCARD

I need a business card for me as a founding consultant in Berlin. I advise entrepreneurs, especially in the design of business ideas, business plans or financing applications. More information about this in the annexes. My USP: I design / structure complex ideas and projects convincingly so that my client is successful. I want to communicate professionalism, effectiveness and clarity. Colors like from the range BLACK-GRAY-GREEN. I am 27 years old, I have studied business for 7 years. Attachments: - Business card design (only idea, do not focus on it) - Website screenshot (only idea, do not focus on it)

Target Market(s)

Target group: Founder (20-50 yrs, m / w, needy, in "break-up phase") and CONTRACTOR / "financier" (30-55 yrs, m / w, often public service "routine-oriented"). The foundations are in quite different industries: digital, craft, tourism, retail, services, etc. Almost all German.

Industry/Entity Type

Consultant

Contact Information for Business Card

Lukas Brennwald
M. Sc., International Business Administration
Gründungsberater, Konzeptentwickler
www.kelvoran-mitrel.de
Postfach-Zugang@kelvoran.de
Tel. 0481 294 3172

Colors

Designer to choose colors to be used in the design.

Requirements
Must have
• Professionalism, persuasiveness, clarity
Nice to have
• memorability
Should not have
• Schnörkelei

```html
<!DOCTYPE html>
<html lang="de">
<head>
<meta charset="utf-8">
<title>Lukas Brennwald – Visitenkarte</title>
<link href="https://fonts.googleapis.com/css2?family=Rubik:wght@400;500&display=swap" rel="stylesheet">
<style>
  :root {
    --backdrop: #2b2b2c;
    --card-white: #ffffff;
    --panel-dark: #2c2d31;
    --panel-dark-2: #47484d;
    --brand-green: #3fae49;
    --text-light: #d9dadc;
    --text-dark: #2c2d31;
  }
  * { box-sizing: border-box; margin: 0; padding: 0; }
  html, body { width: 1200px; height: 930px; overflow: hidden; }
  body {
    background: var(--backdrop);
    font-family: "Rubik", Arial, sans-serif;
    position: relative;
  }
  .card {
    position: absolute;
    left: 300px;
    width: 600px;
    height: 343px;
    border-radius: 22px;
    background: var(--card-white);
    overflow: hidden;
    box-shadow: 0 10px 28px rgba(0,0,0,.45);
  }
  .card--front { top: 95px; }
  .card--back { top: 492px; }

  .brand {
    position: absolute;
    display: flex;
    align-items: center;
    gap: 12px;
  }
  .brand__square {
    width: 26px; height: 26px;
    background: var(--brand-green);
  }
  .brand__name {
    font-weight: 500;
    font-size: 24px;
    color: var(--brand-green);
    letter-spacing: .5px;
    white-space: nowrap;
  }
  .card--front .brand { left: 50%; top: 128px; transform: translateX(-50%); }
  .front__url {
    position: absolute;
    bottom: 34px;
    width: 100%;
    text-align: center;
    color: var(--brand-green);
    font-size: 15px;
    letter-spacing: .4px;
  }

  .back__panel {
    position: absolute;
    left: 205px; top: 0;
    width: 395px; height: 100%;
    background: linear-gradient(160deg, var(--panel-dark-2) 0%, var(--panel-dark) 55%, #232428 100%);
  }
  .back__notch {
    position: absolute;
    left: 205px; top: 138px;
  }
  .card--back .brand {
    left: 0; top: 0;
    width: 205px; height: 100%;
    flex-direction: column;
    justify-content: center;
    gap: 10px;
  }
  .card--back .brand__name { font-size: 17px; }
  .card--back .brand__square { width: 30px; height: 30px; }

  .contact {
    position: absolute;
    left: 250px; top: 62px;
    color: var(--text-light);
  }
  .contact__name {
    color: var(--brand-green);
    font-weight: 500;
    font-size: 28px;
    letter-spacing: .5px;
    margin-bottom: 8px;
  }
  .contact__degree, .contact__role {
    font-size: 15px;
    line-height: 20px;
  }
  .contact__degree span { display: block; padding-left: 20px; }
  .contact__role { margin: 12px 0 0 20px; }
  .contact__list { list-style: none; margin: 14px 0 0 20px; }
  .contact__item {
    display: flex; align-items: center; gap: 10px;
    font-size: 15px; line-height: 22px;
  }
  .contact__item svg { width: 12px; height: 12px; flex: none; }
  .contact__item .accent { color: var(--brand-green); }
</style>
</head>
<body>

<section class="card card--front" aria-label="Vorderseite">
  <div class="brand">
    <span class="brand__square"></span>
    <span class="brand__name">Kelvoran Mitrel</span>
  </div>
  <p class="front__url">www.kelvoran-mitrel.de</p>
</section>

<section class="card card--back" aria-label="Rückseite">
  <div class="back__panel"></div>
  <svg class="back__notch" width="14" height="26" viewBox="0 0 14 26" aria-hidden="true">
    <polygon points="0,0 14,13 0,26" fill="var(--card-white)"/>
  </svg>
  <div class="brand">
    <span class="brand__square"></span>
    <span class="brand__name">Kelvoran Mitrel</span>
  </div>

  <div class="contact">
    <h1 class="contact__name">Lukas Brennwald</h1>
    <p class="contact__degree">M. Sc.,<span>International Business Administration</span></p>
    <p class="contact__role">Gründungsberater,<br>Konzeptentwickler</p>
    <ul class="contact__list">
      <li class="contact__item">
        <svg viewBox="0 0 12 12" aria-hidden="true"><path d="M2.5 1 L4.5 1 L5 3.5 L3.8 4.5 Q5 7 7.5 8.2 L8.5 7 L11 7.5 L11 9.5 Q10.5 11 9 11 Q1 10 1 2.5 Q1 1 2.5 1Z" fill="var(--brand-green)"/></svg>
        0481 294 3172
      </li>
      <li class="contact__item">
        <svg viewBox="0 0 12 12" aria-hidden="true"><rect x="1" y="2.5" width="10" height="7" fill="none" stroke="var(--brand-green)" stroke-width="1.2"/><path d="M1 2.5 L6 6.5 L11 2.5" fill="none" stroke="var(--brand-green)" stroke-width="1.2"/></svg>
        Postfach-Zugang@kelvoran.de
      </li>
      <li class="contact__item">
        <svg viewBox="0 0 12 12" aria-hidden="true"><circle cx="6" cy="6" r="5" fill="none" stroke="var(--brand-green)" stroke-width="1.2"/><ellipse cx="6" cy="6" rx="2.2" ry="5" fill="none" stroke="var(--brand-green)" stroke-width="1"/><path d="M1 6 H11" stroke="var(--brand-green)" stroke-width="1"/></svg>
        <span>www.<span class="accent">kelvoran-mitrel</span>.de</span>
      </li>
    </ul>
  </div>
</section>

</body>
</html>
```